Payment company requires web design

We need a web design for a new company based in Singapore.

The company focuses on providing 2 key products: 1) an alternative payment option (i.e. like quib or trelloquin options) on the traditional checkout process 2) a replacement/outsource of a merchants payment page. Key in the UX flow is a end customer dashboard that manages all payments.

We look to provide a simple, fluid and easy to use payment process. The dashboard is minimalistic that allows easy navigation, review of transactions and all available options through gamification.

The final design should communicate ease of use, flexibility and transparency.

Target Market(s)

The value is for the merchant - retail/travel/insurance companies. However its the merchant's end customers that are the target and who the UX is built for.

Industry/Entity Type

It Company

Logo Text

zelnar

Number of Pages Required

5+ page

Colors
ec1f27

Requirements
Must have
• 7 pages mimicking UX flow
• payment page * 2 - 1) alternative payment type 2) outsource of merchants payment page to our business
• our landing page
• end customer verification page
• end customer registration
• customer dashboard
• UX flow in attached file
Nice to have
• open to ideas
• have asked for the logo to be added
• logo to have the colour red (chinese for prosperity)
• the company is all about flexibility, transparency in personal finance management with the option of instalment payments

```html
<!DOCTYPE html>
<html lang="en">
<head>
<meta charset="utf-8">
<title>Zelnar — Payment processing from Singapore</title>
<link href="https://fonts.googleapis.com/css2?family=Raleway:wght@300;400;600;700&family=Open+Sans:wght@400;600;700&display=swap" rel="stylesheet">
<style>
:root{
  --red:#ec1f27;
  --ink:#333333;
  --muted:#777777;
  --light:#ffffff;
  --footer:#f0f0f0;
  --hero-a:#1c2536;
  --hero-b:#3b4350;
  --about-a:#1d2630;
  --about-b:#3a4048;
}
*{margin:0;padding:0;box-sizing:border-box}
html,body{width:1200px;height:3030px;overflow:hidden}
body{position:relative;background:#fff;font-family:'Open Sans',sans-serif;color:var(--ink)}
.abs{position:absolute}
.center{left:0;width:1200px;text-align:center}
.nowrap{white-space:nowrap}

/* hero */
.hero{top:0;left:0;width:1200px;height:700px;background:linear-gradient(180deg,var(--hero-a) 0%,#2a3140 45%,var(--hero-b) 100%)}
.hero-shade{top:0;left:0;width:1200px;height:700px;background:radial-gradient(ellipse at 50% 70%,rgba(120,110,100,.35),rgba(0,0,0,0) 60%)}
.logo{top:36px;left:72px;font-family:'Raleway',sans-serif;font-size:34px;font-weight:600;color:var(--light);letter-spacing:1px}
.nav a{position:absolute;top:49px;font-family:'Raleway',sans-serif;font-size:13px;font-weight:600;color:var(--light);text-decoration:none;letter-spacing:.5px}
.btn-reg{top:36px;left:970px;width:151px;height:39px;background:var(--red);color:#fff;font-family:'Raleway',sans-serif;font-weight:700;font-size:13px;display:flex;align-items:center;justify-content:center;gap:8px;border-radius:2px}
.hero-title{top:248px;font-family:'Raleway',sans-serif;font-weight:400;font-size:54px;color:var(--light);letter-spacing:2px}
.hero-sub{top:318px;font-family:'Raleway',sans-serif;font-size:27px;color:var(--light)}
.hero-sub b{font-weight:700}
.pill{top:380px;width:112px;height:32px;border:1.5px solid rgba(255,255,255,.85);border-radius:3px;color:#fff;font-family:'Raleway',sans-serif;font-size:10px;font-weight:700;display:flex;align-items:center;justify-content:center;letter-spacing:.5px}
.btn-red{background:var(--red);color:#fff;font-family:'Raleway',sans-serif;font-weight:700;font-size:12px;display:flex;align-items:center;justify-content:center;gap:7px;border-radius:2px}
.slide-dots span{position:absolute;left:1160px;width:7px;height:7px;border-radius:50%;background:rgba(255,255,255,.35)}

/* what we do */
.sec-title{font-family:'Raleway',sans-serif;font-size:40px;font-weight:300;color:var(--ink)}
.sec-title b{font-weight:700}
.sec-lead{font-size:15px;color:#555}
.card{top:935px;width:333px;height:338px}
.card.active{background:var(--red)}
.card svg{position:absolute;left:54px;top:50px}
.card h3{position:absolute;left:54px;top:162px;font-family:'Raleway',sans-serif;font-size:23px;font-weight:600;color:var(--ink)}
.card p{position:absolute;left:54px;top:203px;width:240px;font-size:13px;line-height:26px;color:var(--muted)}
.card.active h3,.card.active p{color:#fff}

/* about */
.about{top:1374px;left:0;width:1200px;height:505px;background:linear-gradient(120deg,var(--about-a),#2c333b 50%,var(--about-b))}
.about-title{top:1496px;font-family:'Raleway',sans-serif;font-size:38px;font-weight:400;color:#fff}
.about-title b{color:var(--red);font-weight:700}
.about-text{top:1573px;color:#fff;font-size:14px;line-height:34px}

/* solve */
.lead-big{top:2036px;font-family:'Raleway',sans-serif;font-size:21px;color:var(--ink)}
.feature svg{position:absolute;left:0;top:0}
.feature h4{position:absolute;left:77px;top:0;font-size:14.5px;font-weight:700;line-height:27px;color:var(--ink);white-space:nowrap}
.feature p{position:absolute;left:77px;top:70px;font-size:12.5px;line-height:26px;color:var(--muted);white-space:nowrap}
.pager span{position:absolute;top:2328px;width:6px;height:6px;border-radius:50%;background:#ccc}

/* testimonials */
.quote{top:2500px;width:290px}
.quote p{position:absolute;left:26px;top:8px;font-size:12.5px;line-height:23px;color:#666;white-space:nowrap}
.quote .qm{position:absolute;font-family:Georgia,serif;font-size:34px;color:#bbb;line-height:1}
.avatar{width:54px;height:54px;border-radius:50%;background:linear-gradient(#d9dde2,#aab2bb);border:2px solid #eee}
.who{font-size:12px;line-height:20px}
.who b{color:var(--red);font-weight:700;display:block}
.who span{color:var(--muted)}

/* footer */
.footer{top:2759px;left:0;width:1200px;height:211px;background:var(--footer)}
.f-title{font-family:'Raleway',sans-serif;font-size:16px;font-weight:700;color:var(--ink)}
.f-text{font-size:11.5px;line-height:25px;color:#555;white-space:nowrap}
.f-links{list-style:none}
.f-links li{font-size:12px;line-height:26px;color:#555}
.social span{position:absolute;top:2865px;width:28px;height:28px;border-radius:50%}
.copy{top:2988px;font-size:11px;color:#555}
</style>
</head>
<body>

<!-- HERO -->
<div class="abs hero" role="img" aria-label="Night skyline of Singapore with lit towers and waterfront"></div>
<div class="abs hero-shade"></div>
<div class="abs logo">ZELNAR</div>
<nav class="nav">
  <a style="left:541px">HOME</a>
  <a style="left:646px">ABOUT US</a>
  <a style="left:776px">SERVICES</a>
  <a style="left:901px">FAQ</a>
</nav>
<div class="abs btn-reg">
  <svg width="16" height="16" viewBox="0 0 16 16"><rect x="1.5" y="3" width="11" height="11" fill="none" stroke="#fff" stroke-width="1.6"/><path d="M7 9 L14 2" stroke="#fff" stroke-width="2"/></svg>
  REGISTRATION
</div>
<div class="abs center hero-title">ZELNAR</div>
<div class="abs center hero-sub">We are payment processing company from <b>Singapore</b>.</div>
<div class="abs pill" style="left:420px">MERCHANT</div>
<div class="abs pill" style="left:543px">PARTNER</div>
<div class="abs pill" style="left:667px">CUSTOMER</div>
<div class="abs btn-red" style="top:440px;left:521px;width:158px;height:45px">
  <svg width="13" height="13" viewBox="0 0 24 24"><path fill="#fff" d="M6.6 10.8a15 15 0 0 0 6.6 6.6l2.2-2.2a1 1 0 0 1 1-.25 11.4 11.4 0 0 0 3.6.6 1 1 0 0 1 1 1V20a1 1 0 0 1-1 1A17 17 0 0 1 3 4a1 1 0 0 1 1-1h3.5a1 1 0 0 1 1 1c0 1.25.2 2.45.6 3.6a1 1 0 0 1-.25 1z"/></svg>
  CONTACT HERE
</div>
<svg class="abs" style="left:584px;top:616px" width="40" height="40" viewBox="0 0 40 40"><circle cx="20" cy="20" r="18.5" fill="none" stroke="#fff" stroke-width="1.6"/><path d="M13 17 L20 24 L27 17" fill="none" stroke="#fff" stroke-width="1.8"/></svg>
<div class="slide-dots">
  <span style="top:322px;background:#fff"></span><span style="top:345px"></span><span style="top:368px"></span><span style="top:391px"></span>
</div>

<!-- WHAT WE DO -->
<h2 class="abs center sec-title" style="top:784px"><b>What</b> we do</h2>
<p class="abs center sec-lead" style="top:846px">Lorem Ipsum is simply dummy text of the printing and typesetting industry has been the industry's..</p>

<div class="abs card active" style="left:99px">
  <svg width="80" height="90" viewBox="0 0 80 90"><circle cx="42" cy="36" r="28" fill="none" stroke="#fff" stroke-width="6"/><circle cx="42" cy="36" r="10" fill="none" stroke="#fff" stroke-width="5"/><path d="M24 36 Q42 16 60 36 Q42 56 24 36" fill="none" stroke="#fff" stroke-width="4"/><path d="M22 58 L8 80" stroke="#fff" stroke-width="9" stroke-linecap="round"/></svg>
  <h3>Managing fraud</h3>
  <p>Lorem Ipsum is simply dummy text of the printing and typesetting industry. has been the industry...</p>
</div>
<div class="abs card" style="left:434px">
  <svg width="110" height="90" viewBox="0 0 110 90"><rect x="4" y="16" width="70" height="44" rx="6" fill="none" stroke="#666" stroke-width="3"/><path d="M18 60 L16 76 L34 60" fill="#fff" stroke="#666" stroke-width="3" stroke-linejoin="round"/><path d="M40 16 V8 a6 6 0 0 1 6-6 h54 a6 6 0 0 1 6 6 v34 a6 6 0 0 1-6 6 h-26" fill="none" stroke="#666" stroke-width="3"/><path d="M92 48 L96 62 L84 48" fill="none" stroke="#666" stroke-width="3"/></svg>
  <h3>Higher conversion</h3>
  <p>Lorem Ipsum is simply dummy text of the printing and typesetting industry. has been the industry...</p>
</div>
<div class="abs card" style="left:769px">
  <svg width="100" height="90" viewBox="0 0 100 90"><path d="M4 38 H80 L72 82 H12 Z" fill="none" stroke="#666" stroke-width="3" stroke-linejoin="round"/><path d="M20 38 L42 12 L64 38" fill="none" stroke="#666" stroke-width="3"/><path d="M28 50 V72 M42 50 V72 M56 50 V72" stroke="#666" stroke-width="3"/><circle cx="78" cy="34" r="14" fill="#fff" stroke="#666" stroke-width="3"/><path d="M78 26 V40 M72 35 L78 41 L84 35" fill="none" stroke="#666" stroke-width="3"/></svg>
  <h3>Basket size</h3>
  <p>Lorem Ipsum is simply dummy text of the printing and typesetting industry. has been the industry...</p>
</div>

<!-- ABOUT -->
<div class="abs about" role="img" aria-label="Photo of hands working at a laptop on a desk, darkened"></div>
<h2 class="abs center about-title">About <b>Zelnar</b></h2>
<p class="abs center about-text nowrap">Lorem Ipsum is simply dummy text of the printing and typesetting industry. Lorem Ipsum has been the industry's standard<br>dummy text ever since the 1500s, when an unknown printer took a galley of type and scrambled it to make a type specimen book.<br>It has survived not only five centuries...</p>
<div class="abs btn-red" style="top:1707px;left:523px;width:154px;height:40px">READ MORE INFO</div>

<!-- SOLVE -->
<h2 class="abs center sec-title" style="top:1974px">How can we <b>solve your problem?</b></h2>
<p class="abs center lead-big">Lorem Ipsum is simply dummy text of the printing and typesetting industry.</p>

<div class="abs feature" style="left:111px;top:2123px">
  <svg width="56" height="56" viewBox="0 0 56 56"><circle cx="28" cy="28" r="28" fill="var(--red)"/><circle cx="24" cy="30" r="6" fill="none" stroke="#fff" stroke-width="3" stroke-dasharray="3 2"/><circle cx="35" cy="22" r="4" fill="none" stroke="#fff" stroke-width="2.5" stroke-dasharray="2 1.5"/></svg>
  <h4>Lorem Ipsum is simply dummy text of the printing<br>and typesetting industry?</h4>
  <p>Lorem Ipsum is simply dummy text of the printing and typesetting<br>industry. Lorem Ipsum has been the industry's standard dummy<br>text ever since the 1500s...</p>
</div>
<div class="abs feature" style="left:625px;top:2123px">
  <svg width="56" height="56" viewBox="0 0 56 56"><circle cx="28" cy="28" r="28" fill="var(--red)"/><rect x="18" y="16" width="14" height="18" fill="none" stroke="#fff" stroke-width="2.5"/><rect x="24" y="22" width="14" height="18" fill="var(--red)" stroke="#fff" stroke-width="2.5"/></svg>
  <h4>Lorem Ipsum is simply dummy text of the printing<br>and typesetting industry?</h4>
  <p>Lorem Ipsum is simply dummy text of the printing and typesetting<br>industry. Lorem Ipsum has been the industry's standard dummy<br>text ever since the 1500s...</p>
</div>
<div class="pager"><span style="left:586px;background:var(--red)"></span><span style="left:597px"></span><span style="left:608px"></span></div>

<!-- TESTIMONIALS -->
<h2 class="abs center sec-title" style="top:2410px">What our <b>Client's</b> say</h2>

<div class="abs quote" style="left:105px">
  <span class="qm" style="left:0;top:0">“</span>
  <p>Lorem Ipsum is simply dummy text of the<br>printing and typesetting industry. Lorem<br>Ipsum has been the industry's standard<br>dummy text ever since...</p>
  <span class="qm" style="left:268px;top:78px">”</span>
</div>
<div class="abs quote" style="left:455px">
  <span class="qm" style="left:0;top:0">“</span>
  <p>Lorem Ipsum is simply dummy text of the<br>printing and typesetting industry. Lorem<br>Ipsum has been the industry's standard<br>dummy text ever since...</p>
  <span class="qm" style="left:268px;top:78px">”</span>
</div>
<div class="abs quote" style="left:816px">
  <span class="qm" style="left:0;top:0">“</span>
  <p>Lorem Ipsum is simply dummy text of the<br>printing and typesetting industry. Lorem<br>Ipsum has been the industry's standard<br>dummy text ever since...</p>
  <span class="qm" style="left:268px;top:78px">”</span>
</div>

<div class="abs avatar" style="left:102px;top:2627px" role="img" aria-label="Client portrait"></div>
<div class="abs who" style="left:172px;top:2636px"><b>MARTEN HOLBY</b><span>Business man</span></div>
<div class="abs avatar" style="left:452px;top:2627px" role="img" aria-label="Client portrait"></div>
<div class="abs who" style="left:522px;top:2636px"><b>MARTEN HOLBY</b><span>Business man</span></div>
<div class="abs avatar" style="left:812px;top:2627px" role="img" aria-label="Client portrait"></div>
<div class="abs who" style="left:883px;top:2636px"><b>MARTEN HOLBY</b><span>Business man</span></div>

<!-- FOOTER -->
<footer class="abs footer"></footer>
<h5 class="abs f-title" style="left:101px;top:2798px">Privacy Policy</h5>
<p class="abs f-text" style="left:101px;top:2828px">Lorem Ipsum is simply dummy text of the printing and typesetting<br>industry. Lorem Ipsum has been the industry...</p>
<div class="abs btn-red" style="top:2895px;left:101px;width:109px;height:34px;font-family:'Open Sans',sans-serif;font-weight:400;font-size:13px">Read more</div>

<h5 class="abs f-title" style="left:519px;top:2798px">Welcome</h5>
<ul class="abs f-links" style="left:519px;top:2827px"><li>Home</li><li>About</li><li>Services</li><li>Faq</li></ul>

<h5 class="abs f-title" style="left:675px;top:2798px">Contact Info</h5>
<p class="abs f-text" style="left:675px;top:2829px;line-height:22px">120 Street name, City name,<br>Country name : 385664</p>
<div class="abs f-text" style="left:675px;top:2879px;display:flex;align-items:center;gap:6px">
  <svg width="11" height="11" viewBox="0 0 24 24"><path fill="var(--red)" d="M6.6 10.8a15 15 0 0 0 6.6 6.6l2.2-2.2a1 1 0 0 1 1-.25 11.4 11.4 0 0 0 3.6.6 1 1 0 0 1 1 1V20a1 1 0 0 1-1 1A17 17 0 0 1 3 4a1 1 0 0 1 1-1h3.5a1 1 0 0 1 1 1c0 1.25.2 2.45.6 3.6a1 1 0 0 1-.25 1z"/></svg>
  ( 555 ) 410 - 2290
</div>
<div class="abs f-text" style="left:675px;top:2905px;display:flex;align-items:center;gap:6px">
  <svg width="12" height="10" viewBox="0 0 12 10"><rect x=".75" y=".75" width="10.5" height="8.5" fill="none" stroke="var(--red)" stroke-width="1.3"/><path d="M1 1 L6 5.5 L11 1" fill="none" stroke="var(--red)" stroke-width="1.3"/></svg>
  info@zelnar.com
</div>

<h5 class="abs f-title" style="left:907px;top:2798px">Follow us</h5>
<p class="abs f-text" style="left:907px;top:2828px">Connect with our social network</p>
<div class="social">
  <span style="left:909px;background:#3b5a98"></span>
  <span style="left:943px;background:#41a9dd"></span>
  <span style="left:977px;background:#d7222a"></span>
  <span style="left:1011px;background:#444"></span>
  <span style="left:1045px;background:#1b86bc"></span>
</div>

<p class="abs center copy">Copyright © 2016, Zelnar. All Rights Reserved</p>

</body>
</html>
```